Building company buisness cards

We are looking for a sharp modern new look for our business cards.We are a New Zealand based company that specialises in house and land packages.We have attached a photo of the current logo and would like to see if it can be improved somehow if needed.We are open to any colours but we have chosen Black and White at this stage. Feel free to change the font and make the logo smarter looking.Play with the colours and see what looks best.We want a card that looks so good know one will want to throw it away!

Target Market(s)

Building profesonals, home buyers

Industry/Entity Type

Building

Contact Information for Business Card

Garrick Tenwood
0275390628
garrickt@hartvale.co.nz

Font styles to use
Serif
Sans Serif

Colors

Designer to choose colors to be used in the design.

Requirements
Must have
• Just the logo on one side and details on the other
• Clean simple looking card
Nice to have
• Round corners and detail like raised or spot UV
• Something that stands out
Should not have
• To title needed, Director etc

```html
<!DOCTYPE html>
<html lang="en">
<head>
<meta charset="utf-8">
<title>Hartvale Business Card</title>
<link rel="stylesheet" href="https://fonts.googleapis.com/css2?family=Roboto:wght@400;500;700;900&display=swap">
<style>
  :root {
    --backdrop: #e6e6e6;
    --card-white: #ffffff;
    --navy: #1e2a5a;
    --orange: #ed9b22;
    --text-grey: #4a4a4a;
    --divider: #d0d0d0;
  }
  * { margin: 0; padding: 0; box-sizing: border-box; }
  html, body {
    width: 1125px;
    height: 1200px;
    overflow: hidden;
    background: var(--backdrop);
    font-family: "Roboto", Arial, sans-serif;
  }
  .canvas { position: relative; width: 1125px; height: 1200px; }
  .card {
    position: absolute;
    left: 151px;
    width: 800px;
    height: 456px;
    border-radius: 24px;
  }
  .card-front { top: 103px; background: var(--card-white); }
  .card-back { top: 619px; background: var(--orange); }

  .brand {
    position: absolute;
    right: 412px;
    top: 200px;
    display: flex;
    align-items: center;
    gap: 14px;
  }
  .brand-name {
    font-weight: 900;
    font-size: 50px;
    color: var(--navy);
    letter-spacing: 0.5px;
    line-height: 1;
  }
  .brand-circle {
    width: 54px; height: 54px;
    border: 3px solid var(--orange);
    border-radius: 50%;
  }
  .divider {
    position: absolute;
    left: 424px;
    top: 147px;
    width: 1px;
    height: 163px;
    background: var(--divider);
  }
  .contact { position: absolute; left: 461px; top: 162px; }
  .contact-name {
    font-weight: 700;
    font-size: 29px;
    color: var(--navy);
    margin-bottom: 20px;
  }
  .contact-line {
    display: flex;
    align-items: center;
    gap: 11px;
    font-size: 19px;
    color: var(--text-grey);
    height: 25.5px;
  }
  .contact-line svg { width: 18px; height: 18px; fill: var(--navy); flex: none; }

  .back-ring {
    position: absolute;
    left: 304px; top: 132px;
    width: 194px; height: 194px;
    border: 9px solid var(--card-white);
    border-radius: 50%;
  }
  .back-web {
    position: absolute;
    left: 0; right: 0;
    top: 390px;
    text-align: center;
    color: var(--card-white);
    font-size: 18px;
    letter-spacing: 8px;
  }
</style>
</head>
<body>
<div class="canvas">
  <section class="card card-front">
    <div class="brand">
      <span class="brand-name">HARTVALE</span>
      <span class="brand-circle"></span>
    </div>
    <div class="divider"></div>
    <div class="contact">
      <p class="contact-name">Garrick Tenwood</p>
      <p class="contact-line">
        <svg viewBox="0 0 24 24" aria-hidden="true"><path d="M6.6 10.8a15.1 15.1 0 0 0 6.6 6.6l2.2-2.2a1 1 0 0 1 1-.25 11.4 11.4 0 0 0 3.6.57 1 1 0 0 1 1 1V20a1 1 0 0 1-1 1A17 17 0 0 1 3 4a1 1 0 0 1 1-1h3.5a1 1 0 0 1 1 1c0 1.25.2 2.45.57 3.57a1 1 0 0 1-.25 1z"/></svg>
        0275390628
      </p>
      <p class="contact-line">
        <svg viewBox="0 0 24 24" aria-hidden="true"><path d="M2 5h20v14H2zm2 2v.5l8 5 8-5V7zm0 2.8V17h16V9.8l-8 5z"/></svg>
        garrickt@hartvale.co.nz
      </p>
      <p class="contact-line">
        <svg viewBox="0 0 24 24" aria-hidden="true"><path d="M12 2a10 10 0 1 0 0 20 10 10 0 0 0 0-20zm-1 17.9A8 8 0 0 1 4.2 10.6L9 15.4v1a2 2 0 0 0 2 2zm6.9-2.5a2 2 0 0 0-1.9-1.4h-1v-3a1 1 0 0 0-1-1H8v-2h2a1 1 0 0 0 1-1V7h2a2 2 0 0 0 2-2v-.4a8 8 0 0 1 2.9 12.8z"/></svg>
        www.hartvale.co.nz
      </p>
    </div>
  </section>

  <section class="card card-back">
    <div class="back-ring"></div>
    <p class="back-web">www.Hartvale.co.nz</p>
  </section>
</div>
</body>
</html>
```